Hartwell Estates Business Cards

I would like a business card that includes myself and my partner.
Includes: Logo, office #, email, website, our names, our numbers and possibly the address. I would also like the logo to be embossed and the card to be horizontal.
There is a photo of our yard signs to give you an idea of the colors of our business.

Target Market(s)

Everyone in real estate market.
We are in a rural area. Our clientele are from all socioeconomic backgrounds.

Industry/Entity Type

Real Estate Agent

Contact Information for Business Card

Company Name: Hartwell Estates
Our Names, Titles & Cell #'s : Dana Pembrook-Broker (555).317.6624, Marla Pembrook-Realtor (555).609.1385
Office #: (555).240.3918
Website: hartwellestates-demo.com
Joint Email: pembrook@hartwellestates-demo.com
Office Address: 418B W. Calloway Ave.
Millbrook, OK. 70913

Font styles to use
Serif

Requirements
Must have
• HORIZONTAL, Logo, Myself and my partners names, Our cell #'s, our office #, our website, our email address
Nice to have
• Embossed logo, office address, our titles.

```html
<!DOCTYPE html>
<html lang="en">
<head>
<meta charset="utf-8">
<title>Hartwell Estates Business Cards</title>
<link rel="stylesheet" href="https://fonts.googleapis.com/css2?family=EB+Garamond:wght@600&family=Source+Sans+3:wght@400;600&display=swap">
<style>
  :root {
    --plum: #4a2366;
    --ink: #2b2b2b;
    --paper: #ffffff;
    --backdrop: #ecebee;
    --sans: "Source Sans 3", Arial, sans-serif;
    --serif: "EB Garamond", Georgia, serif;
  }
  * { margin: 0; padding: 0; box-sizing: border-box; }
  html, body { width: 1200px; height: 900px; overflow: hidden; }
  body { background: var(--backdrop); position: relative; font-family: var(--sans); }

  .card {
    position: absolute;
    background: var(--paper);
    box-shadow: 0 8px 24px rgba(0,0,0,0.15);
    overflow: hidden;
  }
  .card--contacts { left: 238px; top: 62px; width: 555px; height: 341px; }
  .card--brand { left: 457px; top: 519px; width: 560px; height: 342px; }

  .agent { position: absolute; top: 50px; color: var(--ink); }
  .agent--broker { left: 37px; }
  .agent--realtor { right: 71px; text-align: right; }
  .agent__name { font-weight: 600; font-size: 19px; color: var(--plum); line-height: 1.1; }
  .agent__title { font-size: 15px; line-height: 1.3; }
  .agent__phone { font-size: 15px; margin-top: 10px; display: flex; align-items: center; gap: 6px; }
  .agent--realtor .agent__phone { justify-content: flex-end; }

  .icon { width: 12px; height: 12px; fill: currentColor; flex: none; }
  .agent .icon { fill: var(--plum); }

  .office-band {
    position: absolute; left: 0; top: 160px; width: 555px; height: 158px;
    background: var(--plum); color: var(--paper);
  }
  .office-band__address { position: absolute; left: 37px; top: 30px; font-size: 15px; line-height: 20px; }
  .office-band__contacts { position: absolute; left: 37px; top: 82px; font-size: 15px; line-height: 20px; list-style: none; }
  .office-band__contacts li { display: flex; align-items: center; gap: 8px; }
  .office-band__mark {
    position: absolute; right: 48px; top: 28px;
    display: flex; flex-direction: column; align-items: center; gap: 8px;
    font-family: var(--serif); font-weight: 600; font-size: 28px; line-height: 1.05;
    color: var(--paper); text-align: center;
  }
  .mark-dot { width: 22px; height: 22px; border-radius: 50%; background: var(--paper); }

  .brand-mark {
    position: absolute; inset: 0;
    display: flex; align-items: center; justify-content: center; gap: 16px;
    font-family: var(--serif); font-weight: 600; font-size: 44px; color: var(--plum);
  }
  .brand-mark .mark-dot { width: 44px; height: 44px; background: var(--plum); }
</style>
</head>
<body>
  <svg width="0" height="0" style="position:absolute">
    <symbol id="i-phone" viewBox="0 0 24 24"><path d="M6.6 10.8a15.1 15.1 0 0 0 6.6 6.6l2.2-2.2a1 1 0 0 1 1-.25 11.4 11.4 0 0 0 3.6.57 1 1 0 0 1 1 1V20a1 1 0 0 1-1 1A17 17 0 0 1 3 4a1 1 0 0 1 1-1h3.5a1 1 0 0 1 1 1c0 1.25.2 2.45.57 3.57a1 1 0 0 1-.25 1z"/></symbol>
    <symbol id="i-mail" viewBox="0 0 24 24"><path d="M2 5h20v14H2zm2 2v.5l8 5.5 8-5.5V7z"/></symbol>
    <symbol id="i-globe" viewBox="0 0 24 24"><circle cx="12" cy="12" r="10"/></symbol>
  </svg>

  <section class="card card--contacts">
    <div class="agent agent--broker">
      <p class="agent__name">Dana Pembrook</p>
      <p class="agent__title">Broker</p>
      <p class="agent__phone"><svg class="icon"><use href="#i-phone"/></svg>(555).317.6624</p>
    </div>
    <div class="agent agent--realtor">
      <p class="agent__name">Marla Pembrook</p>
      <p class="agent__title">Realtor</p>
      <p class="agent__phone">(555).609.1385<svg class="icon"><use href="#i-phone"/></svg></p>
    </div>
    <div class="office-band">
      <p class="office-band__address">418B W. Calloway Ave.<br>Millbrook, OK. 70913</p>
      <ul class="office-band__contacts">
        <li><svg class="icon"><use href="#i-phone"/></svg>(555).240.3918</li>
        <li><svg class="icon"><use href="#i-mail"/></svg>pembrook@hartwellestates-demo.com</li>
        <li><svg class="icon"><use href="#i-globe"/></svg>hartwellestates-demo.com</li>
      </ul>
      <div class="office-band__mark"><span class="mark-dot"></span><span>Hartwell<br>Estates</span></div>
    </div>
  </section>

  <section class="card card--brand">
    <div class="brand-mark"><span class="mark-dot"></span>Hartwell Estates</div>
  </section>
</body>
</html>
```